dobbo's business card for earthmoving and tipper hire business.

I have a small earthmoving and tipper truck company. I am aiming for the smaller jobs that the big guys don't want. I am also Doing grass slashing and fire hazard reduction work. I would like to see some earthy colors, greens browns etc. I have a tractor with a front end loader attachment, and a 22 ton tipper. I would like to maybe have a silhouette of a tipper and tractor/slasher/loader setup in centre with my business name over the top and details to one side or something like that

Industry/Entity Type

Business

Contact Information for Business Card

Dobbo's small earthworks and tipper hireToowoombaABN: 47781050480PH 0479126773Email dobbo.3@farrowpost.com

Font styles to use
Sans Serif

Colors
fbee3d
abd036
85cae6
f78f20

Requirements
Nice to have
• Earthy colors . business name in blue

```html
<!DOCTYPE html>
<html lang="en">
<head>
<meta charset="utf-8">
<title>Dobbo's small earthworks and tipper hire – business card</title>
<link rel="stylesheet" href="https://fonts.googleapis.com/css2?family=PT+Sans:wght@400;700&display=swap">
<style>
  :root {
    --backdrop: #b9c0cc;
    --leaf-green: #acd036;
    --sun-yellow: #fbee3d;
    --soft-yellow: #f3ea3a;
    --stone-grey: #c4c4c2;
  }
  * { margin: 0; padding: 0; box-sizing: border-box; }
  html, body {
    width: 1200px;
    height: 1000px;
    overflow: hidden;
    background: var(--backdrop);
    font-family: "PT Sans", Arial, sans-serif;
  }
  .stage { position: relative; width: 1200px; height: 1000px; }

  .card { position: absolute; width: 841px; height: 480px; }

  /* Back side: identity */
  .card-back {
    left: 313px; top: 470px;
    background: var(--sun-yellow);
  }
  .brand-name {
    position: absolute; left: 0; width: 100%; top: 618px;
    text-align: center;
    font-size: 38px; font-weight: 700; letter-spacing: 3px;
    color: var(--stone-grey);
  }
  .vehicles-art {
    position: absolute; left: 307px; top: 215px;
    width: 228px; height: 62px;
    background: var(--stone-grey);
    border-radius: 6px;
  }
  .tagline {
    position: absolute; left: 0; width: 100%; top: 288px;
    text-align: center;
    font-size: 17px;
    color: var(--stone-grey);
  }
  .divider-rule { position: absolute; left: 220px; top: 374px; }

  /* Front side: details */
  .card-front {
    left: 53px; top: 62px;
    background: var(--leaf-green);
  }
  .card-front .base-band {
    position: absolute; left: 0; bottom: 0; width: 100%; height: 62px;
    background: var(--sun-yellow);
  }
  .contact-list {
    position: absolute; left: 62px; top: 190px;
    display: grid; grid-template-columns: 83px auto;
    row-gap: 2px;
    font-size: 24px; line-height: 32px;
    color: var(--soft-yellow);
  }
  .column-rule {
    position: absolute; left: 478px; top: 122px;
  }
  .service-list {
    position: absolute; right: 63px; top: 168px;
    list-style: none; text-align: right;
    font-size: 22px; line-height: 28px; letter-spacing: 0.5px;
    color: var(--soft-yellow);
  }
</style>
</head>
<body>
<main class="stage">

  <section class="card card-back" aria-label="Card back">
    <div class="vehicles-art" role="img" aria-label="Silhouettes of a tractor with front end loader and a tipper truck"></div>
    <p class="tagline">small earthworks and tipper hire</p>
    <svg class="divider-rule" width="400" height="20" viewBox="0 0 400 20" aria-hidden="true">
      <line x1="20" y1="10" x2="380" y2="10" stroke="var(--stone-grey)" stroke-width="3"/>
      <circle cx="13" cy="10" r="7" fill="var(--stone-grey)"/>
      <circle cx="30" cy="10" r="7" fill="var(--stone-grey)"/>
      <circle cx="370" cy="10" r="7" fill="var(--stone-grey)"/>
      <circle cx="387" cy="10" r="7" fill="var(--stone-grey)"/>
    </svg>
  </section>
  <h1 class="brand-name" style="left:313px;width:841px;">DOBBO'S</h1>

  <section class="card card-front" aria-label="Card front">
    <dl class="contact-list">
      <dt>ABN</dt><dd>: 51603928174</dd>
      <dt>Phone</dt><dd>: 0412 583 906</dd>
      <dt>Email</dt><dd>: dobbo.3@farrowpost.com</dd>
    </dl>
    <svg class="column-rule" width="6" height="240" viewBox="0 0 6 240" aria-hidden="true">
      <path d="M3 0 Q5 120 3 240 Q1 120 3 0 Z" fill="var(--soft-yellow)"/>
    </svg>
    <ul class="service-list">
      <li>small earthworks</li>
      <li>slashing</li>
      <li>fire hazard reduction</li>
      <li>rural cleanups</li>
      <li>tipper</li>
    </ul>
    <div class="base-band"></div>
  </section>

</main>
</body>
</html>
```